BOLD & MINIMALIST DESIGN NEEDED

We want a very bold but minimalistic business card design that is impactful and utilizes both sides of the business card. Our current logo is included for your use.

We want bold fonts and good use of negative space. We don't want the logo to overpower the design.

Target Market(s)

Professionals who are building new commercial buildings.

Industry/Entity Type

Construction

Contact Information for Business Card

Name, Title, email, office phone, cell phone, website

Font styles to use
Serif
Sans Serif

Requirements
Must have
• Bold design!

```html
<!DOCTYPE html>
<html lang="en">
<head>
<meta charset="utf-8">
<title>Ridgeway Design + Build — Business Card</title>
<link href="https://fonts.googleapis.com/css2?family=Montserrat:wght@400;500;700;800&display=swap" rel="stylesheet">
<style>
  :root {
    --lime: #84c441;
    --lime-deep: #3f7a2c;
    --ink: #111111;
    --paper: #ffffff;
    --stage: #3a3a3a;
  }
  * { box-sizing: border-box; margin: 0; padding: 0; }
  html, body { width: 1200px; height: 689px; overflow: hidden; }
  body {
    background: var(--stage);
    font-family: "Montserrat", sans-serif;
    display: flex;
    align-items: center;
    justify-content: center;
    gap: 40px;
  }
  .card {
    position: relative;
    width: 540px;
    height: 309px;
    border-radius: 22px;
    overflow: hidden;
  }
  .card-front {
    background: var(--lime);
    display: flex;
    align-items: center;
    justify-content: center;
  }
  .wordmark {
    display: flex;
    align-items: center;
    gap: 12px;
    font-weight: 800;
    text-transform: uppercase;
    line-height: 1;
  }
  .wordmark-square {
    width: 22px;
    height: 22px;
  }
  .card-front .wordmark { color: var(--lime-deep); font-size: 40px; }
  .card-front .wordmark-square { background: var(--lime-deep); width: 30px; height: 30px; }
  .wordmark-sub {
    display: block;
    font-size: 0.36em;
    letter-spacing: 0.42em;
    margin-top: 8px;
  }
  .card-back { background: var(--paper); }
  .card-back .curve { position: absolute; inset: 0; }
  .card-back .wordmark {
    position: absolute;
    left: 34px;
    top: 170px;
    color: var(--ink);
    font-size: 30px;
  }
  .card-back .wordmark-square { background: var(--lime); }
  .contact {
    position: absolute;
    left: 345px;
    top: 34px;
    color: var(--paper);
    list-style: none;
    font-size: 11.5px;
    line-height: 1.55;
  }
  .contact-name { font-weight: 800; font-size: 21px; letter-spacing: 0.02em; line-height: 1.1; }
  .contact-title { font-weight: 500; margin-bottom: 8px; }
  .contact-address { margin-bottom: 8px; }
  .contact-line { display: flex; align-items: center; gap: 7px; }
  .contact-line svg { width: 11px; height: 11px; flex: none; }
</style>
</head>
<body>
  <section class="card card-front" aria-label="Card front">
    <div class="wordmark">
      <span class="wordmark-square"></span>
      <span>Ridgeway<span class="wordmark-sub">Design + Build</span></span>
    </div>
  </section>

  <section class="card card-back" aria-label="Card back">
    <svg class="curve" viewBox="0 0 540 309" preserveAspectRatio="none" aria-hidden="true">
      <path d="M292 0 C258 130 330 268 540 300 L540 309 L540 0 Z" fill="var(--ink)"/>
      <path d="M318 0 C292 130 360 262 540 292 L540 0 Z" fill="var(--paper)"/>
      <path d="M324 0 C300 128 366 258 540 288 L540 0 Z" fill="var(--lime)"/>
    </svg>

    <div class="wordmark">
      <span class="wordmark-square"></span>
      <span>Ridgeway<span class="wordmark-sub">Design + Build</span></span>
    </div>

    <ul class="contact">
      <li class="contact-name">MARCUS BELL</li>
      <li class="contact-title">OWNER-CEO</li>
      <li class="contact-address">Your address, City<br>State, Zip 1234</li>
      <li class="contact-line">
        <svg viewBox="0 0 12 12"><path d="M2 1h3l1 3-2 1a7 7 0 0 0 3 3l1-2 3 1v3c-5 1-10-4-9-9z" fill="currentColor"/></svg>
        123 456 789
      </li>
      <li class="contact-line">
        <svg viewBox="0 0 12 12"><rect x="3" y="0.5" width="6" height="11" rx="1.2" fill="none" stroke="currentColor"/><circle cx="6" cy="9.6" r="0.7" fill="currentColor"/></svg>
        123 456 789
      </li>
      <li class="contact-line">
        <svg viewBox="0 0 12 12"><rect x="0.5" y="2" width="11" height="8" fill="currentColor"/><path d="M0.5 2 6 6.5 11.5 2" fill="none" stroke="var(--lime)"/></svg>
        info@yourgmail.com
      </li>
      <li class="contact-line">
        <svg viewBox="0 0 12 12"><circle cx="6" cy="6" r="5.5" fill="currentColor"/><path d="M0.5 6h11M6 0.5c-3 3-3 8 0 11M6 0.5c3 3 3 8 0 11" fill="none" stroke="var(--lime)" stroke-width="0.8"/></svg>
        www.yourwebsite.com
      </li>
    </ul>
  </section>
</body>
</html>
```